Executive Taxi firm with Chauffeur service Website

I have my domain name registered and I have started to work on my site but I am struggling. I am just about to get a logo for the company and need a web site that clearly represents the fact we are an executive/luxury brand in private hire vehicles. We offer airport transfers, train station transfers, seaport transfers, holiday transfers and business to business pick up and drop off.

Target Market(s)

Corporate people, holidaymakers looking for a luxury start their holiday. VIPs' and celebrities.

Number of Pages Required

5+ page

Font styles to use
Serif
Sans Serif
Decorative
Script

Colors

Designer to choose colors to be used in the design.

Requirements
Must have
• Home Page, Services, About Us, VIP and Contact us
• Please see www.brivomotors.co.uk I have started it but not happy with it at all.
Nice to have
• Booking form or enquiry form.

```html
<!DOCTYPE html>
<html lang="en">
<head>
<meta charset="utf-8">
<title>Roadline Travel – Executive Chauffeur Service</title>
<link rel="stylesheet" href="https://fonts.googleapis.com/css2?family=Montserrat:wght@400;600;700;800&family=Open+Sans:wght@400;600&family=Roboto:wght@400;500&display=swap">
<style>
:root{
  --yellow:#f2c500;
  --ink:#222222;
  --body:#444444;
  --white:#ffffff;
  --tile:#f3f1f1;
  --footer:#262626;
  --footer-line:#3a3a3a;
  --panel:rgba(30,30,30,.88);
}
*{box-sizing:border-box;margin:0;padding:0}
html,body{width:1200px;height:3163px;overflow:hidden}
body{position:relative;background:var(--white);font-family:'Open Sans',sans-serif;color:var(--body)}
.abs{position:absolute}
.photo{position:absolute}

/* hero */
.hero{position:absolute;left:0;top:0;width:1200px;height:658px;
  background:linear-gradient(180deg,#9aa2a0 0%,#6f7a63 35%,#4b5a3a 60%,#3b3f3c 100%)}
.brand{position:absolute;display:flex;align-items:center;gap:16px;color:var(--white);
  font-family:'Montserrat',sans-serif;font-weight:800;letter-spacing:.5px}
.brand-mark{width:40px;height:40px;border-radius:50%;background:var(--white)}
.hero .brand{left:142px;top:30px;font-size:26px}
.nav{position:absolute;top:38px;left:605px;display:flex;gap:0}
.nav a{font-family:'Montserrat',sans-serif;font-weight:700;font-size:14px;color:var(--white);
  text-decoration:none;padding:0 16px 10px;position:relative}
.nav a.active{color:var(--yellow)}
.nav a.active::after{content:"";position:absolute;left:16px;right:16px;bottom:0;height:2px;background:var(--yellow)}
.booking{position:absolute;left:627px;top:170px;width:430px;height:348px;background:var(--panel);padding:32px 32px}
.booking h2{font-family:'Montserrat',sans-serif;font-weight:800;font-size:21px;color:var(--white);margin-bottom:24px}
.fields{display:grid;grid-template-columns:1fr 1fr;gap:22px 12px}
.field{height:34px;border:1px solid #cfcfcf;color:#e8e8e8;font-size:12px;padding:0 12px;display:flex;align-items:center;justify-content:space-between}
.submit{margin-top:24px;height:54px;background:var(--yellow);display:flex;align-items:center;justify-content:center;
  font-family:'Montserrat',sans-serif;font-weight:800;font-size:20px;color:var(--ink)}
.dots{position:absolute;top:590px;left:542px;display:flex;gap:12px;align-items:center}
.dots span{width:10px;height:10px;border-radius:50%;background:var(--white)}
.dots span.on{width:14px;height:14px;background:none;border:2px solid var(--white)}

/* welcome */
.rule{position:absolute;height:3px;background:var(--yellow)}
.eyebrow{font-family:'Montserrat',sans-serif;font-weight:700;color:#333;font-size:21px}
.big{font-family:'Montserrat',sans-serif;font-weight:800;color:var(--yellow);font-size:44px;letter-spacing:-.5px}
.para{font-size:14.5px;line-height:20px;color:var(--body)}
.btn{position:absolute;width:110px;height:38px;background:var(--yellow);display:flex;align-items:center;justify-content:center;
  font-family:'Montserrat',sans-serif;font-weight:700;font-size:12px;color:var(--ink)}

/* services */
.tile{position:absolute;background:var(--tile);text-align:center;padding-top:48px;border-right:1px solid #e2dede;border-bottom:1px solid #e2dede}
.tile.hot{background:var(--yellow)}
.tile svg{display:block;margin:0 auto 18px}
.tile h3{font-family:'Montserrat',sans-serif;font-weight:800;font-size:14px;color:var(--ink);line-height:19px;margin-bottom:12px}
.tile.hot h3{color:var(--white)}
.tile p{font-size:12px;line-height:18px;color:#333;width:200px;margin:0 auto}
.svc-title{position:absolute;left:636px;top:1436px;font-family:'Montserrat',sans-serif;color:var(--white);line-height:46px}
.svc-title .l1{font-weight:400;font-size:40px;display:block}
.svc-title .l2{font-weight:800;font-size:40px;display:block}

/* vip */
.heading{font-family:'Montserrat',sans-serif;font-weight:800;color:var(--ink)}

/* testimonials */
.testimonials{position:absolute;left:0;top:2305px;width:1200px;height:473px;background:var(--tile)}
.quote-text{position:absolute;left:345px;top:2503px;width:510px;text-align:center;font-size:14px;line-height:19.5px;color:#444}
.qmark{position:absolute;font-family:'Montserrat',sans-serif;font-weight:800;font-size:70px;color:#bdbdbd;line-height:1}

/* footer */
.footer{position:absolute;left:0;top:2778px;width:1200px;height:385px;background:var(--footer);color:#ddd;font-family:'Roboto',sans-serif}
.footer h4{font-family:'Montserrat',sans-serif;font-weight:700;font-size:11.5px;color:var(--white);margin-bottom:26px}
.fcol{position:absolute;top:70px;font-size:11.5px;line-height:17px}
.fcol ul{list-style:none}
.crow{display:flex;gap:12px;margin-bottom:22px}
.social{display:flex;align-items:center;gap:14px;margin-bottom:14px}
.social i{width:26px;height:26px;border-radius:50%;background:#2f63b0;display:block}
</style>
</head>
<body>

<header class="hero">
  <div role="img" aria-label="White SUV driving on a country road past green fields" class="photo" style="left:0;top:0;width:1200px;height:658px;background:radial-gradient(ellipse at 400px 400px,rgba(230,230,230,.55) 0,rgba(230,230,230,0) 200px)"></div>
  <div class="brand"><span class="brand-mark"></span>ROADLINE TRAVEL</div>
  <nav class="nav">
    <a class="active">HOME</a><a>SERVICES</a><a>ABOUT US</a><a>VIP</a><a>CONTACT US</a>
  </nav>
  <form class="booking">
    <h2>EXECUTIVE ROADLINE TRAVEL</h2>
    <div class="fields">
      <div class="field">First Name</div>
      <div class="field">Last Name</div>
      <div class="field">E mail</div>
      <div class="field">Phone</div>
      <div class="field">Date
        <svg width="12" height="12" viewBox="0 0 12 12"><rect x="1" y="2" width="10" height="9" fill="none" stroke="#ddd"/><line x1="1" y1="5" x2="11" y2="5" stroke="#ddd"/></svg></div>
      <div class="field">Time
        <svg width="13" height="13" viewBox="0 0 13 13"><circle cx="6.5" cy="6.5" r="5.5" fill="none" stroke="#ddd" stroke-width="1.5"/><path d="M6.5 3.5v3h2.5" fill="none" stroke="#ddd" stroke-width="1.3"/></svg></div>
    </div>
    <div class="submit">SUBMIT</div>
  </form>
  <div class="dots"><span></span><span></span><span class="on"></span><span></span><span></span></div>
</header>

<section class="welcome">
  <div role="img" aria-label="Family smiling from the window of a white car" class="photo" style="left:0;top:727px;width:543px;height:416px;background:linear-gradient(135deg,#4b5a33 0%,#7a8a5c 40%,#d9d9d9 75%,#bfc3c4 100%)"></div>
  <div class="abs" style="left:543px;top:727px;width:9px;height:363px;background:var(--yellow)"></div>
  <div class="rule" style="left:624px;top:748px;width:104px"></div>
  <div class="abs eyebrow" style="left:624px;top:768px">WELCOME TO</div>
  <div class="abs big" style="left:622px;top:798px">ROADLINE TRAVEL</div>
  <p class="abs para" style="left:624px;top:892px;width:420px">We provide airport transfers to and from all major UK airports, seaports, train station transfers and an executive business to business transfer service. Whether you have an individual or group transfer request, our company-owned fleet offers a choice of options to suit your needs, from luxury saloons and SUV's to 9-seat luxury transporters.</p>
  <div class="btn" style="left:624px;top:1063px">READ MORE</div>
</section>

<section class="services">
  <div class="tile hot" style="left:0;top:1226px;width:321px;height:276px">
    <svg width="80" height="40" viewBox="0 0 80 40"><path d="M6 30v-9l10-3 9-10h26l11 10 10 3v9z" fill="#222"/><rect x="27" y="11" width="10" height="7" fill="#f2c500"/><rect x="40" y="11" width="12" height="7" fill="#f2c500"/><circle cx="20" cy="31" r="6" fill="#222" stroke="#f2c500" stroke-width="2"/><circle cx="60" cy="31" r="6" fill="#222" stroke="#f2c500" stroke-width="2"/></svg>
    <h3>ALLPORT TRANSFERS</h3>
    <p>Lorem ipsum dolor sit amet, consectetur adipiscing elit. Nam sed lacus sed tellus feugiat lobortis. Quisque consectetur.</p>
  </div>
  <div class="tile" style="left:321px;top:1226px;width:279px;height:276px">
    <svg width="76" height="44" viewBox="0 0 76 44"><path d="M2 8l14-4 8 18-12 6z" fill="#222"/><path d="M74 8l-14-4-8 18 12 6z" fill="#222"/><path d="M20 10l14-3 12 3 10 8-4 6-12-8-8 4z" fill="#222"/><path d="M18 24l10 10 6 4 6-2 12-10-6-6z" fill="#222"/></svg>
    <h3>BUSINESS TO<br>BUSINESS TRANSFERS</h3>
    <p>Lorem ipsum dolor sit amet, consectetur adipiscing elit. Nam sed lacus sed tellus feugiat.</p>
  </div>
  <div class="tile" style="left:0;top:1502px;width:321px;height:267px">
    <svg width="60" height="48" viewBox="0 0 60 48"><rect x="20" y="2" width="20" height="8" fill="none" stroke="#222" stroke-width="4"/><rect x="3" y="10" width="54" height="36" rx="3" fill="#222"/><rect x="14" y="10" width="4" height="36" fill="#fff"/><rect x="42" y="10" width="4" height="36" fill="#fff"/></svg>
    <h3>HOLIDAY TRANSFERS</h3>
    <p>Lorem ipsum dolor sit amet, consectetur adipiscing elit. Nam sed lacus sed tellus feugiat lobortis Quisque consectetur.</p>
  </div>
  <div class="tile" style="left:321px;top:1502px;width:279px;height:267px">
    <svg width="54" height="50" viewBox="0 0 54 50"><path d="M8 30V24a19 19 0 0 1 38 0v6" fill="none" stroke="#222" stroke-width="5"/><rect x="4" y="26" width="10" height="18" rx="3" fill="#222"/><rect x="40" y="26" width="10" height="18" rx="3" fill="#222"/></svg>
    <h3>SUPPORT</h3>
    <p>Lorem ipsum dolor sit amet, consectetur adipiscing elit. Nam sed lacus sed tellus feugiat lobortis Quisque consectetur.</p>
  </div>
  <div role="img" aria-label="Chauffeur in a dark suit opening the door of a black car" class="photo" style="left:600px;top:1226px;width:600px;height:543px;background:linear-gradient(120deg,#3a3a3a 0%,#1c1c1c 45%,#4a4a4a 75%,#202020 100%)"></div>
  <div class="abs" style="left:600px;top:1447px;width:7px;height:73px;background:var(--yellow)"></div>
  <h2 class="svc-title"><span class="l1">OUR</span><span class="l2">SERVICES</span></h2>
</section>

<section class="vip">
  <div role="img" aria-label="Businesswoman working on a laptop in the back seat of a car" class="photo" style="left:0;top:1769px;width:601px;height:536px;background:linear-gradient(180deg,#cfd3d2 0%,#7b7f80 40%,#2c2d30 75%,#1a1a1c 100%)"></div>
  <h2 class="abs heading" style="left:684px;top:1887px;font-size:34px">VIP</h2>
  <div class="rule" style="left:684px;top:1933px;width:52px"></div>
  <p class="abs para" style="left:684px;top:1983px;width:396px">But I must explain to you how all this mistaken idea of denouncing pleasure and praising pain was born and I will give you a complete account of the system, and expound the actual teachings of the great explorer of the truth, the master-builder of human happiness. No one rejects, dislikes, or avoids</p>
  <div class="btn" style="left:684px;top:2155px">READ MORE</div>
</section>

<section class="testimonials"></section>
<h2 class="abs heading" style="left:0;width:1200px;text-align:center;top:2383px;font-size:32px">TESTIMONIALS</h2>
<div class="rule" style="left:574px;top:2437px;width:52px"></div>
<div class="qmark" style="left:328px;top:2466px">“</div>
<p class="quote-text">But I must explain to you how all this mistaken idea of denouncing pleasure and praising pain was born and I will give you a complete account of the system, and expound the actual teachings of the great explorer of the truth, the master-builder of human happiness. No one rejects, dislikes, or avoids pleasure itself, because it is pleasure but because those who do not know how to pursue.</p>
<div class="qmark" style="left:722px;top:2612px">”</div>
<svg class="abs" style="left:140px;top:2555px" width="20" height="28" viewBox="0 0 20 28"><path d="M16 2L4 14l12 12" fill="none" stroke="#aaa" stroke-width="3"/></svg>
<svg class="abs" style="left:1038px;top:2555px" width="20" height="28" viewBox="0 0 20 28"><path d="M4 2l12 12L4 26" fill="none" stroke="#aaa" stroke-width="3"/></svg>
<div role="img" aria-label="Portrait of the client" class="abs" style="left:535px;top:2668px;width:42px;height:42px;border-radius:50%;background:radial-gradient(circle,#b08a70,#5a4a40)"></div>
<div class="abs" style="left:594px;top:2675px;font-family:'Montserrat',sans-serif;font-weight:700;font-size:13px;color:#222">MARTIN</div>
<div class="abs" style="left:594px;top:2693px;font-size:11px;color:#555">Eastfield</div>

<footer class="footer">
  <div class="brand" style="left:148px;top:124px;font-size:26px"><span class="brand-mark"></span>ROADLINE TRAVEL</div>
  <div class="fcol" style="left:502px">
    <h4>CONTACT US</h4>
    <div class="crow"><svg width="10" height="14" viewBox="0 0 10 14"><path d="M5 0a5 5 0 0 1 5 5c0 4-5 9-5 9S0 9 0 5a5 5 0 0 1 5-5z" fill="#fff"/><circle cx="5" cy="5" r="2" fill="#262626"/></svg><span>17 Harbour Row<br>Eastfield, EF4 2QT</span></div>
    <div class="crow"><svg width="12" height="12" viewBox="0 0 12 12"><path d="M2 0l3 3-1.5 2a8 8 0 0 0 3.5 3.5L9 7l3 3-2 2C5 12 0 7 0 2z" fill="#fff"/></svg><span>000.555.0147</span></div>
    <div class="crow"><svg width="13" height="10" viewBox="0 0 13 10"><rect width="13" height="10" fill="#fff"/><path d="M0 0l6.5 5L13 0" fill="none" stroke="#262626"/></svg><span>hello@roadlinetravel.com</span></div>
  </div>
  <div class="fcol" style="left:750px">
    <h4>MENU</h4>
    <ul><li>Home</li><li>Services</li><li>About Us</li><li>VIP</li><li>Contact us</li></ul>
  </div>
  <div class="fcol" style="left:938px">
    <h4>CONNECT WITH US</h4>
    <div class="social"><i></i>Facepage</div>
    <div class="social"><i style="background:#1e9be0"></i>Chirper</div>
    <div class="social"><i style="background:#1c2f5e"></i>ProLink</div>
  </div>
  <div class="abs" style="left:148px;top:272px;width:904px;height:1px;background:var(--footer-line)"></div>
  <div class="abs" style="left:0;width:1200px;text-align:center;top:326px;font-size:11.5px">Copyrights @ 2018 All Rights Reserved</div>
</footer>

</body>
</html>
```